sales brocure for maintenance service company

come up with an eye grabbing sales brochure to highlight our services. we specialize in full facility maintenance we provide janitorial, specialized "cleanroom" cleaning. snow and ice management landscape maintenance, building and facility repair. we only work for commercial, industrial, and educational facilities. you can use some of the photos I uploaded or stock photos our colors are navy blue deep yellow baby/powder blue. I need a design that sells jobs!

```html
<!DOCTYPE html>
<html lang="en">
<head>
<meta charset="utf-8">
<title>Summit Facilities Services – Full Facility Maintenance</title>
<link rel="stylesheet" href="https://fonts.googleapis.com/css2?family=Arimo:wght@700&family=Great+Vibes&display=swap">
<style>
  :root {
    --navy: #1d1f5c;
    --gold: #f5c518;
    --cream: #fde9a6;
    --ink: #0c0c0c;
    --paper: #ffffff;
    --frame: #e9b91d;
  }
  html, body {
    margin: 0;
    padding: 0;
    overflow: hidden;
    background: var(--paper);
  }
  .brochure {
    position: relative;
    width: 1077px;
    height: 1200px;
    overflow: hidden;
    background: var(--paper);
    font-family: "Arimo", Arial, sans-serif;
    font-weight: 700;
    color: var(--ink);
  }
  .brand-panel {
    position: absolute;
    left: 0; top: 0;
    width: 476px; height: 440px;
    border-right: 4px solid var(--frame);
    border-bottom: 4px solid var(--frame);
    display: flex;
    flex-direction: column;
    align-items: center;
    justify-content: center;
    gap: 18px;
  }
  .brand-mark {
    width: 56px; height: 56px;
    border-radius: 50%;
    background: var(--gold);
  }
  .brand-name {
    margin: 0;
    color: var(--navy);
    font-size: 46px;
    line-height: 1.15;
    text-align: center;
    letter-spacing: 1px;
  }
  .brand-location {
    margin: 0;
    color: var(--navy);
    font-size: 34px;
    letter-spacing: 1px;
  }
  .tagline {
    position: absolute;
    left: 493px; top: 4px;
    width: 584px;
    margin: 0;
    font-family: "Great Vibes", cursive;
    font-weight: 400;
    font-size: 72px;
    line-height: 72px;
    text-align: center;
    color: var(--ink);
  }
  .highlight {
    position: absolute;
    height: 34px;
    border-radius: 17px;
    background: var(--cream);
  }
  .highlight--tagline { left: 524px; top: 165px; width: 496px; }
  .highlight--services { left: 7px; top: 540px; width: 760px; }
  .clientele {
    position: absolute;
    left: 510px; top: 205px;
    width: 490px;
    margin: 0;
    font-size: 29px;
    line-height: 40px;
    text-align: center;
  }
  .services-title {
    position: absolute;
    left: 7px; top: 448px;
    margin: 0;
    font-size: 80px;
    line-height: 90px;
    letter-spacing: -1px;
  }
  .service-list {
    position: absolute;
    left: 13px; top: 588px;
    width: 1060px;
    margin: 0; padding: 0;
    list-style: none;
    display: flex;
    align-items: center;
    font-size: 44px;
    line-height: 60px;
  }
  .service-list li { white-space: nowrap; }
  .service-divider {
    width: 9px; height: 58px;
    background: var(--ink);
  }
  .service-list .s1 { margin-right: 100px; }
  .service-list .d1 { margin-right: 56px; }
  .service-list .s2 { margin-right: 60px; }
  .service-list .d2 { margin-right: 42px; }
  .service-photos {
    position: absolute;
    left: 0; top: 652px;
    width: 1077px; height: 456px;
    background:
      linear-gradient(to bottom, rgba(255,255,255,0.55), rgba(255,255,255,0) 18%, rgba(255,255,255,0) 80%, rgba(255,255,255,0.9)),
      linear-gradient(to right, #c9d3da 0%, #a9b6bd 20%, #6f8a4e 30%, #4d7a2e 50%, #6f8f4a 62%, #d9e4ec 72%, #b73a2e 82%, #e9eef3 100%);
  }
  .cta {
    position: absolute;
    left: 0; top: 1112px;
    width: 1077px;
    margin: 0;
    font-size: 46px;
    line-height: 60px;
    text-align: center;
  }
</style>
</head>
<body>
<main class="brochure">
  <header class="brand-panel">
    <span class="brand-mark"></span>
    <h1 class="brand-name">Summit<br>Facilities Services</h1>
    <p class="brand-location">Oakfield, MA</p>
  </header>

  <h2 class="tagline">Specializing in Full<br>Facility Maintenance</h2>
  <span class="highlight highlight--tagline"></span>
  <p class="clientele">We work for<br>Commercial, Industrail, and<br>Educational facilities</p>

  <h2 class="services-title">Services we offer:</h2>
  <span class="highlight highlight--services"></span>
  <ul class="service-list">
    <li class="s1">Wallmoping</li>
    <li class="service-divider d1" aria-hidden="true"></li>
    <li class="s2">Lawn Care</li>
    <li class="service-divider d2" aria-hidden="true"></li>
    <li>Snow Removal</li>
  </ul>

  <div class="service-photos" role="img" aria-label="Photo collage: a worker in a cleanroom suit mopping a wall, two green riding mowers on a lawn, and a red pickup truck plowing snow"></div>

  <p class="cta">Contact us to get your job done today!</p>
</main>
</body>
</html>
```